8'x8' Exhibit Backdrop for Healthcare Events focused on the 55 and older crowds

8X8 Backdrop for Exhibiting.

I also want a design for a 6' table skirt to include our logo on two sides and the logo with Hereditary Cancer Screening underneath on the front. I want the main message of Will You Give your Loved Ones The Information To Beat Cancer in Their Lives to be completely centered on the 8X8 backdrop. Hereditary Cancer Screening The Test You Take For Them in the top left corner and the purple box on the right hand side - just like the photo that has been uploaded below. I need High resolution photos around the backdrop but not so large that they overtake the main message.

Target Market(s)

55+ crowd living in Adult only communities. They have an active lifestyle

Industry/Entity Type

Healthcare

Other font styles liked:
• "The Test You Take For Them" is Comic Sans

Colors
0255a3
fbed22
ffffff

Requirements
Must have
• I am posting a photo of the exact backdrop I would like to see. There are red arrows showing where to move certain items. There is a space underneath the slogan WILL YOU GIVE YOUR LOVED ONES... where another photo will go. Add another photo underneath the slogan that you are moving up - GIVE THEM THE GIFT OF KNOWLEDGE
• See the upload section for the new photo
• Do this one exactly like I am asking for and then you can show me some of your ideas. Thanks
• THE PHOTOS UPLOADED ARE EXAMPLES. FEEL FREE TO SEARCH OUT YOUR OWN HIGH RESOLUTION PHOTOS. THANKS

```html
<!DOCTYPE html>
<html lang="en">
<head>
<meta charset="utf-8">
<title>Hereditary Cancer Screening – Exhibit Backdrop</title>
<link rel="stylesheet" href="https://fonts.googleapis.com/css2?family=Montserrat:wght@400;500;700;800&family=Oswald:wght@400;500;700&display=swap">
<style>
  :root {
    --navy: #0b1f66;
    --green: #7cc242;
    --white: #ffffff;
    --stage: #e9e9e9;
    --ink: #222222;
    --photo-warm-a: #c9a184;
    --photo-warm-b: #8a6a55;
    --photo-green-a: #8fa86b;
    --photo-green-b: #6e5a4a;
    --photo-light-a: #e6d9cc;
    --photo-light-b: #b79f8c;
  }
  * { margin: 0; padding: 0; box-sizing: border-box; }
  html, body { width: 1200px; height: 1200px; overflow: hidden; background: var(--stage); }
  .backdrop {
    position: absolute; left: 20px; top: 132px;
    width: 1270px; height: 1025px;
    background: var(--white);
    transform: scale(0.9134); transform-origin: 0 0;
    font-family: "Montserrat", sans-serif; color: var(--navy);
  }
  .backdrop > * { position: absolute; }

  .title { left: 225px; top: 52px; width: 382px; text-align: right; line-height: 1; }
  .title-main { font-weight: 800; font-size: 61px; letter-spacing: 1px; }
  .title-sub { font-weight: 500; font-size: 58px; display: block; margin-top: -2px; }
  .tagline {
    left: 223px; top: 230px; width: 382px; height: 28px;
    background: var(--green); color: var(--white);
    font-weight: 500; font-size: 21px; line-height: 28px; text-align: center;
  }

  .photo { background: linear-gradient(135deg, var(--photo-warm-a), var(--photo-warm-b)); }
  .photo.outdoor { background: linear-gradient(135deg, var(--photo-green-a), var(--photo-green-b)); }
  .photo.indoor { background: linear-gradient(135deg, var(--photo-light-a), var(--photo-light-b)); }

  .headline { left: 455px; top: 598px; font-family: "Oswald", sans-serif; line-height: 1; }
  .headline-line { display: block; font-size: 49px; font-weight: 400; letter-spacing: -0.5px; white-space: nowrap; }
  .headline-line strong { font-weight: 700; font-size: 60px; }

  .info-rule { left: 443px; top: 715px; width: 14px; height: 310px; background: var(--navy); }
  .info-bar {
    left: 443px; top: 717px; width: 347px; height: 43px; background: var(--navy);
    color: var(--white); font-weight: 700; font-size: 21px; line-height: 43px; padding-left: 30px;
  }
  .cancer { left: 465px; top: 758px; font-family: "Oswald", sans-serif; font-weight: 500; font-size: 72px; letter-spacing: 5px; color: var(--green); line-height: 1; }
  .lives { left: 472px; top: 832px; font-family: "Oswald", sans-serif; font-weight: 500; font-size: 36px; line-height: 1; }
  .base-rule { left: 0; top: 875px; width: 790px; height: 11px; background: var(--navy); }

  .brand-name {
    left: 40px; top: 940px; width: 380px; text-align: center;
    font-weight: 700; font-size: 26px; line-height: 1; letter-spacing: 1.5px; color: var(--navy);
    white-space: nowrap;
  }

  .gift-panel { left: 833px; top: 383px; width: 370px; height: 572px; background: var(--navy); }
  .gift-photo { position: absolute; left: 0; top: 0; width: 100%; height: 400px;
    background: linear-gradient(180deg, #6e5f74 0%, #4b4775 55%, var(--navy) 100%); }
  .gift-text { position: absolute; right: 13px; bottom: 28px; text-align: right; color: var(--white); line-height: 1; }
  .gift-line-lg { display: block; font-family: "Oswald", sans-serif; font-size: 42px; }
  .gift-line-lg b { font-weight: 700; }
  .gift-line-lg span { font-weight: 400; }
  .gift-line-sm { display: block; font-family: "Oswald", sans-serif; font-weight: 400; font-size: 21px; margin: 4px 0 6px; letter-spacing: 0.5px; }
  .gift-note { display: block; font-size: 14px; margin-top: 6px; }
  .gift-note.strong { font-weight: 700; margin-top: 3px; }

  .web { left: 868px; top: 964px; width: 330px; text-align: right; font-weight: 500; font-size: 14px; letter-spacing: 1.5px; color: var(--ink); }
</style>
</head>
<body>
<main class="backdrop">
  <h1 class="title">
    <span class="title-main">Hereditary</span>
    <span class="title-sub">Cancer</span>
    <span class="title-sub">Screening</span>
  </h1>
  <p class="tagline">The Test You Take For Them</p>

  <div class="photo outdoor" style="left:0;top:328px;width:433px;height:210px" role="img" aria-label="Grandmother laughing as two grandchildren kiss her cheeks"></div>
  <div class="photo indoor" style="left:0;top:547px;width:433px;height:206px" role="img" aria-label="Smiling grandparents with two young grandchildren"></div>

  <div class="photo outdoor" style="left:445px;top:280px;width:182px;height:150px" role="img" aria-label="Boy hugging his grandfather outdoors"></div>
  <div class="photo indoor" style="left:636px;top:280px;width:182px;height:150px" role="img" aria-label="Three generations of a family at a table"></div>
  <div class="photo outdoor" style="left:445px;top:438px;width:182px;height:147px" role="img" aria-label="Grandfather and toddler exploring the garden"></div>
  <div class="photo outdoor" style="left:636px;top:438px;width:182px;height:147px" role="img" aria-label="Family sitting together on the grass"></div>

  <div class="photo" style="left:833px;top:62px;width:182px;height:151px" role="img" aria-label="Grandfather and granddaughter cheek to cheek"></div>
  <div class="photo indoor" style="left:1025px;top:62px;width:181px;height:151px" role="img" aria-label="Granddaughter hugging her grandmother"></div>
  <div class="photo outdoor" style="left:833px;top:222px;width:182px;height:150px" role="img" aria-label="Grandparents smiling with a grandchild"></div>
  <div class="photo indoor" style="left:1025px;top:222px;width:181px;height:150px" role="img" aria-label="Grandparents sitting with two grandchildren"></div>

  <h2 class="headline">
    <span class="headline-line">WILL YOU <strong>GIVE</strong></span>
    <span class="headline-line">YOUR LOVED ONES</span>
  </h2>
  <div class="info-rule"></div>
  <p class="info-bar">the information to Beat</p>
  <p class="cancer">CANCER</p>
  <p class="lives">IN THEIR LIVES?</p>
  <div class="base-rule"></div>

  <div class="photo indoor" style="left:468px;top:895px;width:322px;height:110px" role="img" aria-label="Family reading a book together with grandparents"></div>

  <p class="brand-name">KINFOLK WELLNESS</p>

  <section class="gift-panel">
    <div class="gift-photo" role="img" aria-label="Grandmother embracing her granddaughter"></div>
    <div class="gift-text">
      <span class="gift-line-lg"><b>GIVE</b> <span>THEM</span></span>
      <span class="gift-line-sm">THE GIFT OF</span>
      <span class="gift-line-lg"><b>KNOWLEDGE</b></span>
      <span class="gift-note">knowing is better than not knowing.</span>
      <span class="gift-note strong">Knowledge is Power</span>
    </div>
  </section>

  <p class="web">www.kinfolkscreening.com</p>
</main>
</body>
</html>
```